corvale institute of business and technology web site

I need web site for the institute which focus on business courses and computer course it is also for vocation train for employment It is also carear development and advancement .It should have links to online study resource which free
Industry/Entity Type
Business
Number of Pages Required
1 page
Look and feel
Each slider illustrates characteristics of the customer's brand and the style your logo design should communicate.

```html
<!DOCTYPE html>
<html lang="en">
<head>
<meta charset="utf-8">
<title>Corvale Institute of Business and Technology</title>
<link rel="stylesheet" href="https://fonts.googleapis.com/css2?family=Montserrat:wght@400;600;700;800&family=Open+Sans:wght@400;600;700&family=Lora:ital@1&display=swap">
<style>
:root{
  --navy:#1c3d73;
  --navy-deep:#12284d;
  --footer:#1a2f55;
  --green:#6ab04c;
  --lime:#86c440;
  --ink:#2b2b2b;
  --grey:#777;
  --light:#e9eff5;
  --white:#fff;
}
*{box-sizing:border-box;margin:0;padding:0}
html,body{width:1200px;height:3412px;overflow:hidden}
body{position:relative;font-family:"Open Sans",Arial,sans-serif;color:var(--ink);background:var(--white)}
.abs{position:absolute}
h1,h2,h3,h4{font-family:"Montserrat",Arial,sans-serif}

/* header */
.hero-photo{left:0;top:0;width:1200px;height:700px;background:linear-gradient(180deg,#e4e6e8 0%,#f4f4f2 45%,#d9d4cc 70%,#c9c3ba 100%)}
.header-band{left:0;top:0;width:1200px;height:240px}
.top-phone{left:40px;top:6px;font-size:13px;color:var(--white)}
.top-social{right:40px;top:6px;display:flex;gap:6px}
.top-social span{width:16px;height:16px;border-radius:50%;border:1px solid #fff}
.nav{top:96px;font-family:"Montserrat",sans-serif;font-weight:700;font-size:14px;color:var(--white);display:flex;gap:38px;white-space:nowrap}
.nav-left{left:210px}.nav-right{right:210px}
.brand{left:500px;top:22px;width:200px;text-align:center;color:var(--white)}
.brand-mark{width:70px;height:70px;border-radius:50%;background:var(--white);margin:0 auto 10px}
.brand-name{font-family:"Montserrat",sans-serif;font-weight:800;font-size:26px;letter-spacing:2px}
.hero-title{left:0;width:1200px;top:236px;text-align:center;font-family:"Montserrat",sans-serif;font-weight:700;font-size:46px;color:var(--ink)}
.hero-sub{left:0;width:1200px;top:300px;text-align:center;font-size:24px;color:var(--ink)}
.btn-learn{left:540px;top:620px;width:120px;height:36px;background:var(--green);color:#fff;font-size:13px;font-weight:700;text-align:center;line-height:36px;border-radius:3px}

/* course tiles */
.tiles{left:150px;top:690px;width:900px;display:flex;justify-content:space-between}
.tile{width:130px;height:280px;background:var(--white);border-radius:65px;box-shadow:0 4px 14px rgba(0,0,0,.18);text-align:center;padding-top:18px}
.tile-icon{width:94px;height:94px;border-radius:50%;background:var(--navy);margin:0 auto 22px;display:flex;align-items:center;justify-content:center}
.tile-icon.active{background:var(--green)}
.tile-label{font-size:13px;font-weight:700;line-height:17px;padding:0 8px;color:var(--ink)}

/* welcome */
.welcome-kicker{left:0;width:1200px;top:1030px;text-align:center;font-size:15px;font-weight:600;color:var(--ink)}
.welcome-title{left:0;width:1200px;top:1052px;text-align:center;font-size:28px;font-weight:700;color:var(--green)}
.welcome-text{left:70px;width:1060px;top:1102px;text-align:center;font-size:13px;line-height:20px;color:var(--grey)}

/* why */
.why-title{left:0;width:1200px;top:1245px;text-align:center;font-size:30px;font-weight:800;color:var(--ink);white-space:nowrap}
.feature{width:250px}
.feature-num{font-family:"Montserrat",sans-serif;font-size:64px;font-weight:400;color:#bbb;line-height:64px;float:left;margin-right:10px}
.feature h3{font-family:"Open Sans",sans-serif;font-size:19px;font-weight:600;line-height:24px;padding-top:6px;color:var(--ink)}
.feature p{clear:both;font-size:13px;line-height:19px;color:var(--grey);padding-top:10px}
.why-photo{left:615px;top:1330px;width:585px;height:550px;background:linear-gradient(135deg,#d8dde2 0%,#eef1f3 40%,#7a6a5a 75%,#c5ccd2 100%)}

/* banner */
.banner-photo{left:0;top:1880px;width:1200px;height:520px;background:linear-gradient(90deg,#eeeeec 0%,#f6f6f4 35%,#c8a47a 55%,#82bf3e 62%,#86c440 100%)}
.banner-title{left:760px;top:1990px;font-family:"Montserrat",sans-serif;font-weight:800;font-size:50px;color:#111;line-height:56px;white-space:nowrap}
.banner-sub{left:760px;top:2048px;font-family:"Montserrat",sans-serif;font-weight:600;font-size:31px;line-height:38px;color:#111;white-space:nowrap}
.btn-click{left:800px;top:2102px;width:175px;height:44px;background:#111;color:#fff;border-radius:22px;font-family:"Montserrat",sans-serif;font-weight:800;font-size:18px;text-align:center;line-height:44px;white-space:nowrap}

/* testimonials */
.testi-title{left:0;width:1200px;top:2470px;text-align:center;font-size:30px;font-weight:700;color:var(--ink)}
.testi-quote{left:170px;width:860px;top:2560px;text-align:center;font-family:"Lora",Georgia,serif;font-style:italic;font-size:17px;line-height:27px;color:var(--grey)}
.testi-arrow{top:2575px}
.testi-badge{left:588px;top:2672px}
.testi-name{left:0;width:1200px;top:2705px;text-align:center;font-size:11px;color:var(--grey);letter-spacing:1px}
.testi-role{left:0;width:1200px;top:2720px;text-align:center;font-size:10px;color:#999}

/* newsletter */
.news{left:0;top:2740px;width:1200px;height:240px;background:var(--light)}
.news-art{left:170px;top:2760px;width:170px;height:150px;border-radius:8px;background:linear-gradient(135deg,#f4d36a 0%,#5aa0d6 60%,#e9eff5 100%)}
.news-title{left:390px;top:2765px;width:600px;font-size:25px;font-weight:800;line-height:30px;color:var(--green)}
.news-note{left:390px;top:2832px;font-size:17px;font-weight:600;color:var(--ink)}
.field{height:32px;background:#fff;border:1px solid #ccd;font-size:12px;color:#999;padding:7px 10px}
.btn-sub{left:895px;top:2875px;width:130px;height:32px;background:var(--green);color:#fff;font-size:13px;font-weight:700;text-align:center;line-height:32px}
.social{left:500px;top:2920px;display:flex;gap:16px}
.social span{width:50px;height:50px;border-radius:50%;background:var(--navy);border:3px solid #fff;box-shadow:0 2px 6px rgba(0,0,0,.2)}

/* footer */
.footer{left:0;top:2980px;width:1200px;height:400px;background:var(--footer)}
.foot-title{left:60px;top:3030px;font-size:28px;font-weight:800;color:#fff}
.contact-item{left:70px;width:330px;color:#fff;display:flex;gap:20px}
.contact-item svg{flex:none}
.contact-item h4{font-size:13px;font-weight:700;margin-bottom:6px}
.contact-item p{font-size:11px;line-height:17px;color:#c9d3e3}
.msg-title{left:440px;top:3040px;font-size:13px;font-weight:700;color:#fff}
.msg-field{background:var(--footer);border:1px solid #55698f;font-size:11px;color:#8ea0c0;padding:6px 8px}
.btn-submit{left:440px;top:3275px;width:90px;height:30px;background:#2c63c4;color:#fff;font-size:12px;font-weight:700;text-align:center;line-height:30px}
.partner-title{left:880px;top:3060px;font-size:28px;font-weight:800;line-height:30px;color:var(--lime);white-space:nowrap}
.partner-box{left:880px;top:3130px;width:150px;height:110px;background:#000;display:flex;align-items:flex-end;justify-content:center;padding-bottom:16px;color:#fff;font-family:"Montserrat",sans-serif;font-weight:700;font-size:16px;letter-spacing:1px}
.bottom{left:0;top:3380px;width:1200px;height:32px;background:var(--navy-deep);color:#c9d3e3;font-size:11px}
.bottom-links{left:60px;top:9px;display:flex;gap:22px;font-weight:700}
.copyright{right:60px;top:9px}
</style>
</head>
<body>

<div class="abs hero-photo" role="img" aria-label="Bright office desk with a computer monitor, plant, wall clock and glasses"></div>

<svg class="abs header-band" viewBox="0 0 1200 240" aria-hidden="true">
  <path d="M0 0H1200V130H760C730 130 720 150 705 190C695 215 680 232 600 232C520 232 505 215 495 190C480 150 470 130 440 130H0Z" fill="#1c3d73"/>
  <path d="M0 0H1200V30H0Z" fill="#12284d"/>
  <path d="M0 130H440C470 130 480 150 495 190C505 215 520 232 600 232C680 232 695 215 705 190C720 150 730 130 760 130H1200" fill="none" stroke="#6ab04c" stroke-width="4"/>
</svg>
<div class="abs top-phone">+000 211 555 010</div>
<div class="abs top-social"><span></span><span></span><span></span><span></span><span></span></div>
<nav class="abs nav nav-left"><span>HOME</span><span>ABOUT US</span></nav>
<nav class="abs nav nav-right"><span>COURSES</span><span>CONTACT US</span></nav>
<div class="abs brand"><div class="brand-mark"></div><div class="brand-name">CORVALE</div></div>

<h1 class="abs hero-title">Lorem ipsum dolor sit amet</h1>
<p class="abs hero-sub">Lorem ipsum dolor sit amet, consectetur adipiscing elit</p>
<div class="abs btn-learn">LEARN MORE</div>

<section class="abs tiles">
  <div class="tile"><div class="tile-icon"><svg width="50" height="50" viewBox="0 0 50 50"><path d="M25 10L46 20L25 30L4 20Z" fill="#fff"/><path d="M13 25V35C19 40 31 40 37 35V25L25 31Z" fill="#fff"/></svg></div><div class="tile-label">University Education - Long Distance Learning</div></div>
  <div class="tile"><div class="tile-icon"><svg width="50" height="50" viewBox="0 0 50 50"><rect x="10" y="10" width="30" height="32" rx="2" fill="#fff"/><path d="M16 18H34M16 25H34M16 32H28" stroke="#1c3d73" stroke-width="3"/></svg></div><div class="tile-label">Modular Soft Skills</div></div>
  <div class="tile"><div class="tile-icon active"><svg width="50" height="50" viewBox="0 0 50 50"><rect x="8" y="12" width="34" height="22" rx="2" fill="#fff"/><rect x="20" y="36" width="10" height="4" fill="#fff"/></svg></div><div class="tile-label">Direct to Device (D2D)</div></div>
  <div class="tile"><div class="tile-icon"><svg width="50" height="50" viewBox="0 0 50 50"><circle cx="25" cy="21" r="11" fill="#fff"/><rect x="20" y="32" width="10" height="8" fill="#fff"/></svg></div><div class="tile-label">Brightpath</div></div>
  <div class="tile"><div class="tile-icon"><svg width="50" height="50" viewBox="0 0 50 50"><circle cx="25" cy="17" r="8" fill="#fff"/><path d="M10 42C10 30 40 30 40 42Z" fill="#fff"/></svg></div><div class="tile-label">Brightpath Roles in The Talent Continuum</div></div>
  <div class="tile"><div class="tile-icon"><svg width="50" height="50" viewBox="0 0 50 50"><rect x="8" y="17" width="34" height="23" rx="2" fill="#fff"/><path d="M19 17V12H31V17" fill="none" stroke="#fff" stroke-width="3"/></svg></div><div class="tile-label">Business Verticals</div></div>
</section>

<p class="abs welcome-kicker">WELCOME TO</p>
<h2 class="abs welcome-title">CORVALE INSTITUTE OF BUSINESS AND TECHNOLOGY</h2>
<p class="abs welcome-text">Lorem ipsum dolor sit amet, consectetur adipiscing elit, sed do eiusmod tempor incididunt ut labore et dolore magna aliqua. Ut enim ad minim veniam, quis nostrud exercitation ullamco laboris nisi ut aliquip ex ea commodo consequat. Duis aute irure dolor in reprehenderit in voluptate velit esse cillum dolore eu fugiat nulla pariatur excepteur sint occaecat cupidatat non proident.</p>

<h2 class="abs why-title">WHY CHOOSE CORVALE INSTITUTE OF BUSINESS AND TECHNOLOGY</h2>
<div class="abs feature" style="left:60px;top:1345px"><span class="feature-num">01</span><h3>Over 50 years of experience</h3><p>Duis autem vel eum iriure dolor in hendrerit in vulputate velit esse molestie consequat, vel illum dolore eu feugiat nulla facilisis at vero eros et accumsan.</p></div>
<div class="abs feature" style="left:340px;top:1345px"><span class="feature-num">02</span><h3>We are passionate</h3><p>Duis autem vel eum iriure dolor in hendrerit in vulputate velit esse molestie consequat, vel illum dolore eu feugiat nulla facilisis at vero eros et accumsan.</p></div>
<div class="abs feature" style="left:60px;top:1600px"><span class="feature-num">03</span><h3>We are fast, accuracy &amp; reliable</h3><p>Duis autem vel eum iriure dolor in hendrerit in vulputate velit esse molestie consequat, vel illum dolore eu feugiat nulla facilisis at vero eros et accumsan.</p></div>
<div class="abs feature" style="left:340px;top:1600px"><span class="feature-num">04</span><h3>We are improving everyday</h3><p>Duis autem vel eum iriure dolor in hendrerit in vulputate velit esse molestie consequat, vel illum dolore eu feugiat nulla facilisis at vero eros et accumsan.</p></div>
<div class="abs why-photo" role="img" aria-label="Young professional standing in a modern open-plan office"></div>

<div class="abs banner-photo" role="img" aria-label="Student lying on a wooden floor studying on a laptop, against a green backdrop"></div>
<h2 class="abs banner-title">ONLINE STUDY</h2>
<p class="abs banner-sub">RESOURCE WHICH FREE</p>
<div class="abs btn-click">CLICK HERE</div>

<h2 class="abs testi-title">CLIENT'S TESTIMONIALS</h2>
<svg class="abs testi-arrow" style="left:80px" width="24" height="50" viewBox="0 0 24 50"><path d="M20 4L4 25L20 46" fill="none" stroke="#bbb" stroke-width="3"/></svg>
<svg class="abs testi-arrow" style="left:1096px" width="24" height="50" viewBox="0 0 24 50"><path d="M4 4L20 25L4 46" fill="none" stroke="#bbb" stroke-width="3"/></svg>
<p class="abs testi-quote">Lorem ipsum dolor sit amet, consectetur adipiscing elit, sed do eiusmod tempor incididunt ut labore et dolore magna aliqua. Ut enim ad minim veniam, quis nostrud exercitation ullamco laboris nisi ut aliquip ex ea commodo consequat.</p>
<svg class="abs testi-badge" width="24" height="24" viewBox="0 0 24 24"><circle cx="12" cy="12" r="10" fill="none" stroke="#e07b39" stroke-width="2"/><circle cx="12" cy="12" r="4" fill="#e07b39"/></svg>
<p class="abs testi-name">DANIEL MORROW</p>
<p class="abs testi-role">Course Graduate</p>

<section class="abs news"></section>
<div class="abs news-art" role="img" aria-label="Illustration of a student flying on a paper plane"></div>
<h2 class="abs news-title">KEEP IN TOUCH WITH OUR NEWS AND BE THE FIRST ONE TO KNOW</h2>
<p class="abs news-note">Don't worry! we won't spam you, we promise!</p>
<div class="abs field" style="left:390px;top:2875px;width:240px">Enter Your Name</div>
<div class="abs field" style="left:640px;top:2875px;width:240px">Enter Your Email</div>
<div class="abs btn-sub">SUBSCRIBE</div>

<footer class="abs footer"></footer>
<div class="abs social"><span></span><span></span><span></span><span></span><span></span></div>
<h2 class="abs foot-title">GET IN TOUCH NOW!</h2>
<div class="abs contact-item" style="top:3090px"><svg width="24" height="28" viewBox="0 0 24 28"><path d="M12 2C6 2 2 6 2 11C2 18 12 26 12 26C12 26 22 18 22 11C22 6 18 2 12 2Z" fill="#fff"/><circle cx="12" cy="11" r="4" fill="#1a2f55"/></svg><div><h4>ADDRESS</h4><p>1420 Harbor Lane Plaza,<br>Elm Street,<br>Westfield</p></div></div>
<div class="abs contact-item" style="top:3190px"><svg width="24" height="24" viewBox="0 0 24 24"><path d="M5 2L9 2L11 8L8 10C9 13 11 15 14 16L16 13L22 15V19C22 21 20 22 18 22C9 21 3 15 2 6C2 4 3 2 5 2Z" fill="#fff"/></svg><div><h4>PHONE</h4><p>+000 211 555 010, +000 211 555 077</p></div></div>
<div class="abs contact-item" style="top:3270px"><svg width="24" height="20" viewBox="0 0 24 20"><rect x="1" y="2" width="22" height="16" fill="#fff"/><path d="M1 2L12 11L23 2" fill="none" stroke="#1a2f55" stroke-width="2"/></svg><div><h4>EMAIL</h4><p>info@corvaleinstitute.com</p></div></div>

<h3 class="abs msg-title">LEAVE A MESSAGE</h3>
<div class="abs msg-field" style="left:440px;top:3070px;width:180px;height:28px">Name</div>
<div class="abs msg-field" style="left:630px;top:3070px;width:180px;height:28px">Email</div>
<div class="abs msg-field" style="left:440px;top:3110px;width:370px;height:150px">Message</div>
<div class="abs btn-submit">SUBMIT</div>

<h2 class="abs partner-title">IN CONJUNCTION<br>WITH BRIGHTPATH</h2>
<div class="abs partner-box">BRIGHTPATH</div>

<div class="abs bottom">
  <div class="abs bottom-links"><span>HOME</span><span>ABOUT US</span><span>COURSES</span><span>CONTACT US</span></div>
  <div class="abs copyright">© 2015 Corvale Institute Of Business And Technology. All Rights Reserved</div>
</div>

</body>
</html>
```